Boutique Technology Consultancy specialising is Electronic and physical security

We need to redo our existing outdated website. For your reference the link www.pelu.com.au

```html
<!DOCTYPE html>
<html lang="en">
<head>
<meta charset="utf-8">
<title>Pelu Services</title>
<link href="https://fonts.googleapis.com/css2?family=Ubuntu:wght@400;500;700&family=Lato:wght@400;700&display=swap" rel="stylesheet">
<style>
:root{
  --red:#d2232a;
  --red-dark:#7a1f1f;
  --ink:#1b1b1b;
  --grey-text:#555;
  --grey-bg:#f3f3f3;
  --footer:#121212;
  --white:#fff;
}
*{box-sizing:border-box;margin:0;padding:0}
html,body{width:1200px;height:3774px;overflow:hidden}
body{font-family:"Lato",sans-serif;color:var(--ink);background:var(--white)}
.page{position:relative;width:1200px;height:3774px;overflow:hidden}
.abs{position:absolute}
h1,h2,h3,.heading{font-family:"Ubuntu",sans-serif}

/* header */
.topbar{position:absolute;left:454px;top:0;width:746px;height:54px;background:var(--red);clip-path:polygon(0 0,100% 0,100% 100%,36px 100%);color:#fff;font-size:13px;font-weight:700;font-family:"Ubuntu",sans-serif}
.topbar span{position:absolute;top:19px}
.topbar .soc{width:13px;height:13px;border-radius:50%;border:2px solid #fff;top:20px}
.header{position:absolute;left:0;top:0;width:1200px;height:127px;border-bottom:1px solid #e5e5e5}
.brand{position:absolute;display:flex;align-items:center;gap:12px;font-family:"Ubuntu",sans-serif;font-weight:700}
.brand .mark{width:34px;height:34px;background:var(--red)}
.nav a{position:absolute;top:82px;font-family:"Ubuntu",sans-serif;font-size:14px;color:var(--ink);text-decoration:none}
.btn-contact{position:absolute;left:969px;top:68px;width:119px;height:42px;background:var(--red-dark);color:#fff;font-family:"Ubuntu",sans-serif;font-size:13px;font-weight:700;display:flex;align-items:center;justify-content:center}

/* hero */
.hero-bg{position:absolute;left:0;top:128px;width:1200px;height:700px;background:linear-gradient(90deg,#f2f2f2,#e9e9e9)}
.hero-photo{position:absolute;left:580px;top:128px;width:620px;height:680px;background:linear-gradient(135deg,#cfc7bf,#8e8782 55%,#5f5a58)}
.eyebrow{left:110px;top:210px;color:var(--red);font-family:"Ubuntu",sans-serif;font-weight:500;font-size:20px;letter-spacing:3px}
.hero-title{left:110px;top:255px;font-size:46px;font-weight:700;line-height:69px;color:var(--ink)}
.btn-start{left:110px;top:475px;width:165px;height:50px;background:var(--red-dark);color:#fff;font-family:"Ubuntu",sans-serif;font-weight:700;font-size:16px;display:flex;align-items:center;justify-content:center;box-shadow:3px 3px 0 var(--red)}

/* about */
.about-photo{left:112px;top:885px;width:420px;height:545px;background:linear-gradient(160deg,#e9e3da,#b9aea3 50%,#4f5459);border:4px solid #fff;border-radius:0 0 60px 0}
.about-bar{left:600px;top:885px;width:50px;height:5px;background:#fff}
.about-title{left:600px;top:912px;font-size:40px;font-weight:500;color:#fff}
.about-text{left:600px;top:966px;width:480px;color:#fff;font-size:15px;line-height:29px}
.about-text ul{list-style:none;margin:4px 0}
.about-text li{display:flex;align-items:center;gap:10px;line-height:34px}
.about-text li svg{flex:none}
.btn-read{left:600px;top:1243px;width:146px;height:48px;background:#fff;color:var(--red);font-family:"Ubuntu",sans-serif;font-size:15px;font-weight:500;display:flex;align-items:center;justify-content:center}

/* section heads */
.sec-bar{position:absolute;left:574px;width:52px;height:5px;background:var(--red)}
.sec-title{position:absolute;left:0;width:1200px;text-align:center;font-size:40px;font-weight:500;color:var(--ink)}
.sec-title em{font-style:normal;color:var(--red)}
.sec-desc{position:absolute;left:0;width:1200px;text-align:center;font-size:16px;line-height:31px;color:#333}

/* services */
.svc-title{font-family:"Ubuntu",sans-serif;font-size:18px;font-weight:500;color:var(--ink)}
.svc-list{font-size:14px;color:#666;line-height:31px;list-style:none}
.svc-list li{display:flex;align-items:center;gap:8px}
.svc-list.right li{justify-content:flex-end}

/* experience */
.exp-bg{left:0;top:2122px;width:1200px;height:686px;background:var(--grey-bg)}
.card{position:absolute;top:2370px;width:289px;height:348px;background:#fff;border-bottom:4px solid var(--red-dark);text-align:center}
.card .photo{margin:5px;height:202px;background:linear-gradient(160deg,#c9c9c9,#6e6e6e 60%,#3a3a3a)}
.card h3{font-size:18px;font-weight:500;margin-top:16px}
.card p{font-size:12.5px;color:#444;line-height:28px;margin:4px 14px 0}
.arrow{position:absolute;top:2529px;width:28px;height:28px;border-radius:50%;background:var(--red)}

/* contact */
.info{position:absolute;left:112px;display:flex;gap:13px}
.info .ic{width:62px;height:62px;border-radius:50%;background:linear-gradient(135deg,var(--red),var(--red-dark));flex:none;display:flex;align-items:center;justify-content:center}
.info h4{font-family:"Ubuntu",sans-serif;font-size:17px;font-weight:700;letter-spacing:1px;margin-top:-2px}
.info p{font-family:"Ubuntu",sans-serif;font-weight:500;font-size:16px;line-height:28px}
.field{position:absolute;height:50px;background:#fff;box-shadow:0 1px 6px rgba(0,0,0,.12);font-size:14px;color:#555;padding:17px 17px}
.btn-submit{left:510px;top:3248px;width:145px;height:45px;background:var(--red-dark);color:#fff;font-family:"Ubuntu",sans-serif;font-weight:700;font-size:15px;display:flex;align-items:center;justify-content:center;box-shadow:3px 3px 0 var(--red)}

/* footer */
.footer{left:0;top:3370px;width:1200px;height:404px;background:var(--footer);color:#fff}
.foot-h{position:absolute;top:3442px;font-family:"Ubuntu",sans-serif;font-size:20px;font-weight:500;color:#fff}
.foot-list{position:absolute;top:3486px;list-style:none;font-size:15px;color:#fff}
.foot-list li{height:34.4px;display:flex;align-items:center;gap:10px}
.foot-soc{position:absolute;top:3567px;width:30px;height:30px;border-radius:50%;background:var(--red)}
.foot-contact{position:absolute;left:882px;color:#fff;font-size:15px;line-height:28px;display:flex;gap:14px}
.foot-contact .ic{width:30px;height:30px;border-radius:50%;background:var(--red);flex:none;margin-top:2px}
.rule{left:112px;top:3700px;width:976px;height:1px;background:#555}
.copy{left:0;top:3727px;width:1200px;text-align:center;font-size:14px;color:#fff}
</style>
</head>
<body>
<div class="page">

  <!-- hero background & photo area -->
  <div class="hero-bg"></div>
  <div class="hero-photo" role="img" aria-label="Photo of four business colleagues shaking hands around a laptop in a bright office"></div>

  <!-- red chevron band -->
  <svg class="abs" style="left:0;top:0" width="1200" height="1400" viewBox="0 0 1200 1400">
    <path d="M0 600 L760 790 L1200 600 L1200 1368 L0 1368 Z" fill="#d2232a"/>
    <path d="M0 588 L760 778 L1200 588 L1200 604 L760 796 L0 604 Z" fill="#fff"/>
    <path d="M165 640 L760 800 L1135 690 L760 828 Z" fill="#5e1c1c"/>
  </svg>

  <!-- header -->
  <header class="header">
    <div class="brand" style="left:112px;top:30px;font-size:52px;color:var(--ink)"><span class="mark"></span>PELU</div>
    <nav class="nav">
      <a style="left:437px">HOME</a>
      <a style="left:535px">EXPERIENCE</a>
      <a style="left:674px">SERVICES</a>
      <a style="left:794px">TEAM</a>
      <a style="left:891px">ABOUT</a>
    </nav>
    <div class="btn-contact">CONTACT US</div>
  </header>
  <div class="topbar">
    <svg class="abs" style="left:42px;top:19px" width="13" height="13" viewBox="0 0 24 24"><path d="M6.6 10.8a15 15 0 0 0 6.6 6.6l2.2-2.2c.3-.3.7-.4 1-.2 1.1.4 2.3.6 3.6.6.6 0 1 .4 1 1V20c0 .6-.4 1-1 1A17 17 0 0 1 3 4c0-.6.4-1 1-1h3.5c.6 0 1 .4 1 1 0 1.3.2 2.5.6 3.6.1.3 0 .7-.2 1z" fill="#fff"/></svg>
    <span style="left:66px">CALL US: 1300 555 014</span>
    <svg class="abs" style="left:273px;top:20px" width="14" height="11" viewBox="0 0 14 11"><rect width="14" height="11" rx="1" fill="#fff"/><path d="M0 1 L7 6 L14 1" stroke="#d2232a" stroke-width="1.4" fill="none"/></svg>
    <span style="left:297px">MAIL US: HELLO@PELU.COM.AU</span>
    <span class="soc" style="left:554px"></span>
    <span class="soc" style="left:585px"></span>
    <span class="soc" style="left:617px"></span>
  </div>

  <!-- hero text -->
  <div class="abs eyebrow">WELCOME TO PELU SERVICES</div>
  <h1 class="abs hero-title">YOUR TECHNOLOGY<br>PROJECTS MADE<br>EASY</h1>
  <div class="abs btn-start">GET STARTED</div>

  <!-- about -->
  <div class="abs about-photo" role="img" aria-label="Photo of a young woman typing on a laptop by a bright window"></div>
  <div class="abs about-bar"></div>
  <h2 class="abs about-title">ABOUT PELU</h2>
  <div class="abs about-text">
    <p>Pelu Services was established in 2016 by Dan Merrow to provide technology consulting services to corporate and government clients with a focus on</p>
    <ul>
      <li><svg width="13" height="10" viewBox="0 0 13 10"><path d="M1 5 L5 9 L12 1" stroke="#fff" stroke-width="2.4" fill="none"/></svg>Property/facilities management</li>
      <li><svg width="13" height="10" viewBox="0 0 13 10"><path d="M1 5 L5 9 L12 1" stroke="#fff" stroke-width="2.4" fill="none"/></svg>Asset management</li>
      <li><svg width="13" height="10" viewBox="0 0 13 10"><path d="M1 5 L5 9 L12 1" stroke="#fff" stroke-width="2.4" fill="none"/></svg>Development and Construction</li>
    </ul>
    <p>In 2022, Pelu Services merged Norvale Group into its operations, bringing increased capacity and capability to the NSW office.</p>
  </div>
  <div class="abs btn-read">READ MORE</div>

  <!-- services -->
  <div class="sec-bar" style="top:1498px"></div>
  <h2 class="sec-title" style="top:1520px">OUR <em>SERVICES</em></h2>
  <p class="sec-desc" style="top:1584px">Pelu Services provides independent professional services for projects as well as operations and<br>maintenance. We offer end to end services including:</p>

  <svg class="abs" style="left:0;top:1600px" width="1200" height="480" viewBox="0 1600 1200 480">
    <defs><linearGradient id="ring" x1="0" y1="0" x2="1" y2="1"><stop offset="0" stop-color="#e3262d"/><stop offset="1" stop-color="#7a1f1f"/></linearGradient></defs>
    <circle cx="600" cy="1855" r="160" fill="none" stroke="url(#ring)" stroke-width="26"/>
    <text x="600" y="1872" text-anchor="middle" font-family="Ubuntu, sans-serif" font-weight="700" font-size="46" fill="#1b1b1b">PELU</text>
    <g stroke="#d2232a" stroke-width="2" fill="none">
      <path d="M357 1820 L440 1820"/>
      <path d="M880 1672 L760 1672 L724 1731"/>
      <path d="M833 2040 L760 2040 L724 1979"/>
    </g>
    <g fill="#d2232a">
      <circle cx="357" cy="1820" r="6" stroke="#f5b5b5" stroke-width="4"/>
      <circle cx="880" cy="1672" r="6" stroke="#f5b5b5" stroke-width="4"/>
      <circle cx="833" cy="2040" r="6" stroke="#f5b5b5" stroke-width="4"/>
    </g>
    <!-- strategy icon -->
    <g stroke="#d2232a" stroke-width="2" fill="none">
      <rect x="906" y="1656" width="36" height="26" rx="2"/>
      <path d="M912 1676 L920 1668 L926 1672 L936 1662"/>
      <circle cx="936" cy="1680" r="7"/><path d="M941 1685 L946 1690"/>
    </g>
    <!-- operations icon -->
    <g stroke="#d2232a" stroke-width="2" fill="none">
      <circle cx="316" cy="1800" r="17"/><circle cx="316" cy="1800" r="7"/>
      <path d="M316 1778 V1783 M316 1817 V1822 M294 1800 H299 M333 1800 H338"/>
    </g>
    <!-- projects icon -->
    <g stroke="#d2232a" stroke-width="2" fill="none">
      <circle cx="876" cy="1898" r="18"/><circle cx="876" cy="1898" r="8"/>
      <path d="M876 1874 V1880 M876 1916 V1922 M852 1898 H858 M894 1898 H900 M860 1882 L864 1886 M888 1910 L892 1914"/>
    </g>
  </svg>

  <div class="abs" style="left:903px;top:1702px">
    <div class="svc-title">Strategy</div>
    <ul class="svc-list" style="margin-top:6px">
      <li><svg width="10" height="9" viewBox="0 0 10 9"><path d="M0 4.5 H8 M5 1 L8.5 4.5 L5 8" stroke="#d2232a" stroke-width="2" fill="none"/></svg>Technology roadmaps;</li>
      <li><svg width="10" height="9" viewBox="0 0 10 9"><path d="M0 4.5 H8 M5 1 L8.5 4.5 L5 8" stroke="#d2232a" stroke-width="2" fill="none"/></svg>Master standards; and</li>
      <li><svg width="10" height="9" viewBox="0 0 10 9"><path d="M0 4.5 H8 M5 1 L8.5 4.5 L5 8" stroke="#d2232a" stroke-width="2" fill="none"/></svg>Asset management plans</li>
    </ul>
  </div>

  <div class="abs" style="left:100px;top:1835px;width:242px;text-align:right">
    <div class="svc-title" style="text-align:left;padding-left:15px">Operations &amp; maintenance</div>
    <ul class="svc-list right" style="margin-top:0">
      <li>Service and maintenance<svg width="10" height="9" viewBox="0 0 10 9"><path d="M10 4.5 H2 M5 1 L1.5 4.5 L5 8" stroke="#d2232a" stroke-width="2" fill="none"/></svg></li>
      <li style="padding-right:18px">specifications;</li>
      <li>Policies and procedures;<svg width="10" height="9" viewBox="0 0 10 9"><path d="M10 4.5 H2 M5 1 L1.5 4.5 L5 8" stroke="#d2232a" stroke-width="2" fill="none"/></svg></li>
      <li style="padding-right:18px">Procurement; and</li>
      <li>Service reviews<svg width="10" height="9" viewBox="0 0 10 9"><path d="M10 4.5 H2 M5 1 L1.5 4.5 L5 8" stroke="#d2232a" stroke-width="2" fill="none"/></svg></li>
    </ul>
  </div>

  <div class="abs" style="left:851px;top:1932px">
    <ul class="svc-list">
      <li><svg width="10" height="9" viewBox="0 0 10 9"><path d="M0 4.5 H8 M5 1 L8.5 4.5 L5 8" stroke="#d2232a" stroke-width="2" fill="none"/></svg>Audit;Design;Procurement;</li>
      <li><svg width="10" height="9" viewBox="0 0 10 9"><path d="M0 4.5 H8 M5 1 L8.5 4.5 L5 8" stroke="#d2232a" stroke-width="2" fill="none"/></svg>Technical project management; &amp;</li>
      <li><svg width="10" height="9" viewBox="0 0 10 9"><path d="M0 4.5 H8 M5 1 L8.5 4.5 L5 8" stroke="#d2232a" stroke-width="2" fill="none"/></svg>Witness testing</li>
    </ul>
    <div class="svc-title" style="margin-top:4px">Projects</div>
  </div>

  <!-- experience -->
  <div class="abs exp-bg"></div>
  <div class="sec-bar" style="top:2188px"></div>
  <h2 class="sec-title" style="top:2210px">OUR <em>EXPERIENCE</em></h2>
  <p class="sec-desc" style="top:2275px">Pelu has a diverse range of project experience across a range of industries within both the public and private<br>sectors. The following is a small sample of some of the clients and sites we have worked with.</p>

  <div class="card" style="left:112px">
    <div class="photo" role="img" aria-label="Black and white photo of a historic brick tower under a glass cone roof"></div>
    <h3>Harbour Central</h3>
    <p>Security technology design consulting for this popular retail and entertainment hub which is managed by the Lantern Group.</p>
  </div>
  <div class="card" style="left:455px">
    <div class="photo" role="img" aria-label="Black and white photo of a motorway gantry over passing cars"></div>
    <h3>RingLink</h3>
    <p>Virtual servers, network and CCTV upgrade design and project management for this landmark road transportation Public Private</p>
  </div>
  <div class="card" style="left:799px">
    <div class="photo" role="img" aria-label="Black and white photo of a modern hospital entrance at dusk"></div>
    <h3>Northgate Women's Hospital</h3>
    <p>Security technology lifecycle consulting for this leading Health Care Public Private Partnership (PPP)</p>
  </div>
  <div class="arrow" style="left:38px"><svg width="28" height="28" viewBox="0 0 28 28"><path d="M16 9 L11 14 L16 19" stroke="#fff" stroke-width="2.4" fill="none"/></svg></div>
  <div class="arrow" style="left:1123px"><svg width="28" height="28" viewBox="0 0 28 28"><path d="M12 9 L17 14 L12 19" stroke="#fff" stroke-width="2.4" fill="none"/></svg></div>

  <!-- contact -->
  <div class="sec-bar" style="top:2876px"></div>
  <h2 class="sec-title" style="top:2898px">GET IN <em>TOUCH WITH US</em></h2>

  <div class="info" style="top:2985px">
    <div class="ic"><svg width="18" height="24" viewBox="0 0 18 24"><path d="M9 0C4 0 0 4 0 9c0 7 9 15 9 15s9-8 9-15c0-5-4-9-9-9z" fill="#fff"/><circle cx="9" cy="9" r="3.5" fill="#b8232a"/></svg></div>
    <div><h4>LOCATION</h4><p>GPO Box 4120<br>CARLTON VIC 3053</p></div>
  </div>
  <div class="info" style="top:3111px">
    <div class="ic"><svg width="22" height="22" viewBox="0 0 24 24"><path d="M6.6 10.8a15 15 0 0 0 6.6 6.6l2.2-2.2c.3-.3.7-.4 1-.2 1.1.4 2.3.6 3.6.6.6 0 1 .4 1 1V20c0 .6-.4 1-1 1A17 17 0 0 1 3 4c0-.6.4-1 1-1h3.5c.6 0 1 .4 1 1 0 1.3.2 2.5.6 3.6.1.3 0 .7-.2 1z" fill="#fff"/></svg></div>
    <div><h4>PHONE NUMBER</h4><p>1300 555 014</p></div>
  </div>
  <div class="info" style="top:3226px">
    <div class="ic"><svg width="22" height="16" viewBox="0 0 22 16"><rect width="22" height="16" rx="2" fill="#fff"/><path d="M0 2 L11 9 L22 2" stroke="#b8232a" stroke-width="2" fill="none"/></svg></div>
    <div><h4>EMAIL ADDRESS</h4><p>hello@pelu.com.au</p></div>
  </div>

  <div class="field" style="left:508px;top:2985px;width:283px">First Name</div>
  <div class="field" style="left:803px;top:2985px;width:282px">Your Email</div>
  <div class="field" style="left:508px;top:3048px;width:283px">Your Phone</div>
  <div class="field" style="left:803px;top:3048px;width:282px">Services
    <svg class="abs" style="right:14px;top:22px" width="10" height="6" viewBox="0 0 10 6"><path d="M0 0 H10 L5 6 Z" fill="#222"/></svg>
  </div>
  <div class="field" style="left:508px;top:3111px;width:577px;height:111px">Message</div>
  <div class="abs btn-submit">SUBMIT</div>

  <!-- footer -->
  <footer class="abs footer"></footer>
  <div class="brand" style="left:112px;top:3462px;font-size:54px;color:#fff"><span class="mark"></span>PELU</div>
  <span class="foot-soc" style="left:112px"></span>
  <span class="foot-soc" style="left:170px"></span>
  <span class="foot-soc" style="left:228px"></span>
  <span class="foot-soc" style="left:285px"></span>

  <div class="foot-h" style="left:430px">QUICK LINKS</div>
  <ul class="foot-list" style="left:430px">
    <li><svg width="13" height="12" viewBox="0 0 13 12"><path d="M0 6 H10 M6 1 L11 6 L6 11" stroke="#fff" stroke-width="2.4" fill="none"/></svg>Home</li>
    <li><svg width="13" height="12" viewBox="0 0 13 12"><path d="M0 6 H10 M6 1 L11 6 L6 11" stroke="#fff" stroke-width="2.4" fill="none"/></svg>About</li>
    <li><svg width="13" height="12" viewBox="0 0 13 12"><path d="M0 6 H10 M6 1 L11 6 L6 11" stroke="#fff" stroke-width="2.4" fill="none"/></svg>Experience</li>
    <li><svg width="13" height="12" viewBox="0 0 13 12"><path d="M0 6 H10 M6 1 L11 6 L6 11" stroke="#fff" stroke-width="2.4" fill="none"/></svg>Team</li>
    <li><svg width="13" height="12" viewBox="0 0 13 12"><path d="M0 6 H10 M6 1 L11 6 L6 11" stroke="#fff" stroke-width="2.4" fill="none"/></svg>Contact Us</li>
  </ul>

  <div class="foot-h" style="left:688px">HELP LINKS</div>
  <ul class="foot-list" style="left:688px">
    <li><svg width="13" height="12" viewBox="0 0 13 12"><path d="M0 6 H10 M6 1 L11 6 L6 11" stroke="#fff" stroke-width="2.4" fill="none"/></svg>FAQ</li>
    <li><svg width="13" height="12" viewBox="0 0 13 12"><path d="M0 6 H10 M6 1 L11 6 L6 11" stroke="#fff" stroke-width="2.4" fill="none"/></svg>Terms of use</li>
    <li><svg width="13" height="12" viewBox="0 0 13 12"><path d="M0 6 H10 M6 1 L11 6 L6 11" stroke="#fff" stroke-width="2.4" fill="none"/></svg>Privacy Policy</li>
    <li><svg width="13" height="12" viewBox="0 0 13 12"><path d="M0 6 H10 M6 1 L11 6 L6 11" stroke="#fff" stroke-width="2.4" fill="none"/></svg>Support Links</li>
    <li><svg width="13" height="12" viewBox="0 0 13 12"><path d="M0 6 H10 M6 1 L11 6 L6 11" stroke="#fff" stroke-width="2.4" fill="none"/></svg>Conditions</li>
  </ul>

  <div class="foot-h" style="left:882px">CONTACT US</div>
  <div class="foot-contact" style="top:3484px"><span class="ic"></span><span>GPO Box 4120<br>CARLTON VIC 3053</span></div>
  <div class="foot-contact" style="top:3556px"><span class="ic"></span><span>1300 555 014</span></div>
  <div class="foot-contact" style="top:3608px"><span class="ic"></span><span>hello@pelu.com.au</span></div>

  <div class="abs rule"></div>
  <div class="abs copy">Copyrights@2023.Pelu Services.All Rights Reserved</div>
</div>
</body>
</html>
```